"Vine Hollow Excursions" is a top notch Santa Barbara County Wine Tour company.

We provide scenic, boutique and custom wine tours. I need the card to be clean and classy. I will provide our logo. I would like the logo to cover the back side of the card as an option and would like to see a couple color options other then our signature green and gold. I would like to see some creative options and let the designers come up with options.
I need cards for myself and my team. The final design should communicate "An authentic and boutique wine tour experience"
Please use my website for reference www.vinehollowexcursions.example

Target Market(s)

We have a wide range of clients from millennials to baby boomers

Industry/Entity Type

Tour

Contact Information for Business Card

Contact info:
Dale Morton
805-219-6384
info@vinehollowexcursions.example
vinehollowexcursions.example

Colors

Designer to choose colors to be used in the design.

Requirements
Must have
• my logo
Nice to have
• *I would like to have the backside side with the logo and the company statement
• "An authentic and boutique wine tour experience" as an option.
• *I would also like to see what the designers can create!
• *I would like to see an option that incorporates or social: instagram, yelp, trip advisor
Should not have
• I do not want it too busy.

```html
<!DOCTYPE html>
<html lang="en">
<head>
<meta charset="utf-8">
<title>Vine Hollow Excursions — Business Card</title>
<link href="https://fonts.googleapis.com/css2?family=Cinzel:wght@400;500&family=Arimo:wght@400&display=swap" rel="stylesheet">
<style>
  :root{
    --backdrop:#4a443e;
    --card-white:#ffffff;
    --brand-green:#3f6b46;
    --ink-green:#5d7f63;
    --rule-green:#7c9a80;
    --sky-top:#2c3848;
    --sky-low:#4a5564;
    --vine-dark:#2b2a1e;
    --vine-mid:#4d4b2a;
    --on-photo:#ffffff;
  }
  *{box-sizing:border-box;margin:0;padding:0}
  html,body{width:1200px;height:930px;overflow:hidden}
  body{background:var(--backdrop);position:relative;font-family:"Arimo",Arial,sans-serif}

  .card{position:absolute;width:600px;height:343px;box-shadow:0 10px 28px rgba(0,0,0,.45)}

  .card--front{left:80px;top:80px;overflow:hidden}
  .card__photo{position:absolute;inset:0;
    background:linear-gradient(180deg,var(--sky-top) 0%,var(--sky-low) 34%,var(--vine-mid) 52%,var(--vine-dark) 100%)}
  .card__brand-front{position:absolute;left:0;right:0;top:150px;text-align:center;
    font-family:"Cinzel",serif;font-weight:400;font-size:34px;letter-spacing:2px;color:var(--on-photo)}

  .card--back{left:520px;top:487px;background:var(--card-white)}
  .card__brand-back{position:absolute;left:36px;top:150px;width:250px;text-align:center;
    font-family:"Cinzel",serif;font-weight:400;font-size:24px;line-height:1.3;letter-spacing:1px;color:var(--brand-green)}
  .card__divider{position:absolute;left:318px;top:88px;width:1px;height:170px;background:var(--rule-green)}
  .contact{position:absolute;left:336px;top:88px;color:var(--ink-green);font-size:13px;line-height:1.45}
  .contact__name{font-family:"Cinzel",serif;font-size:22px;color:var(--brand-green);line-height:1.1}
  .contact__role{margin-bottom:6px}
  .contact__address{margin-bottom:6px}
  .contact__row{display:flex;align-items:center;gap:8px;font-size:12.5px}
  .contact__row svg{width:11px;height:11px;flex:none}
</style>
</head>
<body>

  <section class="card card--front">
    <div class="card__photo" role="img" aria-label="Photograph of vineyard rows on rolling hills under a dusk sky"></div>
    <div class="card__brand-front">Vine Hollow Excursions</div>
  </section>

  <section class="card card--back">
    <div class="card__brand-back">Vine Hollow<br>Excursions</div>
    <div class="card__divider"></div>
    <div class="contact">
      <div class="contact__name">Dale Morton</div>
      <div class="contact__role">Founder</div>
      <div class="contact__address">418 Quarry Ln.<br>Los Olivos, CA 93441</div>
      <div class="contact__row">
        <svg viewBox="0 0 12 12"><path d="M3 1l2 2.5-1.2 1.2a7 7 0 0 0 3.5 3.5L8.5 7 11 9l-1.3 1.8C5.5 10.5 1.5 6.5 1.2 2.3z" fill="var(--ink-green)"/></svg>
        805-219-6384
      </div>
      <div class="contact__row">
        <svg viewBox="0 0 12 12"><rect x="1" y="2.5" width="10" height="7" fill="none" stroke="var(--ink-green)" stroke-width="1.2"/><path d="M1 2.5l5 4 5-4" fill="none" stroke="var(--ink-green)" stroke-width="1.2"/></svg>
        info@vinehollowexcursions.example
      </div>
      <div class="contact__row">
        <svg viewBox="0 0 12 12"><circle cx="6" cy="6" r="5" fill="none" stroke="var(--ink-green)" stroke-width="1.1"/><ellipse cx="6" cy="6" rx="2.2" ry="5" fill="none" stroke="var(--ink-green)" stroke-width="1"/><path d="M1 6h10" stroke="var(--ink-green)" stroke-width="1"/></svg>
        www.vinehollowexcursions.example
      </div>
    </div>
  </section>

</body>
</html>
```